Professional Business Card - TWO SIDES

I need a new business card design to be used by myself and my employees. I would like a professional card and for the front I thought I would like a dark blue thatch with our logo in a raised gold foil on top of it. On the other side I would like name, position, and contact info. I've uploaded our old design for an example of the info used.

Target Market(s)

Business Clients

Industry/Entity Type

CPA Firm

Contact Information for Business Card

Logo, Name, Title, Address, Phone Numbers, Website address, Email Address

Font styles to use
Serif
Sans Serif

Colors
0054AA
0677BA
7BADD7
CADEEF
E8F1F8
0094D4
00A9DD
6FCCEA
C7EBF8
E9F6FB

Requirements
Must have
• Modern Professional Look
Nice to have
• Logo in Gold Foil or ability to have is raised. I like our logo in a single color
Should not have
• I've uploaded old business card

```html
<!DOCTYPE html>
<html lang="en">
<head>
<meta charset="utf-8">
<title>Hale &amp; Hale CPA – Business Card</title>
<link rel="stylesheet" href="https://fonts.googleapis.com/css2?family=Arimo:wght@400;700&display=swap">
<style>
  :root {
    --page-bg: #ebebe9;
    --card-bg: #2e2e2e;
    --card-edge: #9ccc2c;
    --accent: #9ccc2c;
    --text-light: #f2f2f2;
    --text-muted: #d9d9d9;
    --rule: #9a9a9a;
    --mark-tone: #3a3a3a;
  }
  * { margin: 0; padding: 0; box-sizing: border-box; }
  html, body {
    width: 1200px; height: 801px; overflow: hidden;
    background: var(--page-bg);
    font-family: "Arimo", Arial, sans-serif;
  }
  .sheet {
    position: relative; width: 1200px; height: 801px;
    display: flex; align-items: center; justify-content: center; gap: 60px;
  }
  .card {
    position: relative; width: 520px; height: 297px;
    background: var(--card-bg);
    border-bottom: 4px solid var(--card-edge);
    border-right: 2px solid var(--card-edge);
    box-shadow: 0 6px 18px rgba(0,0,0,0.18);
    overflow: hidden; color: var(--text-light);
  }
  .wordmark { display: flex; flex-direction: column; align-items: flex-start; }
  .wordmark-name {
    display: flex; align-items: center; gap: 10px;
    font-weight: 700; font-size: 34px; letter-spacing: 1px; color: var(--text-light);
    line-height: 1;
  }
  .wordmark-dot { width: 14px; height: 14px; background: var(--accent); }
  .wordmark-tagline {
    margin-top: 6px; font-weight: 700; font-size: 11.5px; letter-spacing: 3.2px;
    color: var(--text-light);
  }
  /* info side */
  .card-info .wordmark { position: absolute; top: 40px; left: 150px; }
  .card-info .divider {
    position: absolute; left: 40px; right: 40px; top: 124px;
    height: 1px; background: var(--rule);
  }
  .person { position: absolute; left: 40px; top: 140px; }
  .person-name { font-weight: 700; font-size: 22px; color: var(--accent); line-height: 1.1; }
  .person-title { font-size: 14px; color: var(--text-muted); margin-top: 4px; padding-bottom: 6px; border-bottom: 1px solid var(--rule); width: 150px; }
  .contacts { position: absolute; left: 40px; top: 204px; list-style: none; }
  .contacts li {
    display: flex; align-items: center; gap: 10px;
    font-size: 14px; color: var(--text-light); line-height: 22px;
  }
  .contacts svg { width: 13px; height: 13px; flex: none; }
  .address {
    position: absolute; right: 40px; top: 140px; text-align: right;
    font-size: 14px; font-style: normal; line-height: 22px; color: var(--text-light);
  }
  /* logo side */
  .card-brand .mark-area {
    position: absolute; left: 20px; top: 20px; width: 230px; height: 260px;
    background: radial-gradient(ellipse at 45% 50%, var(--mark-tone) 0%, rgba(46,46,46,0) 70%);
  }
  .card-brand .wordmark { position: absolute; right: 38px; bottom: 48px; }
</style>
</head>
<body>
<main class="sheet">
  <section class="card card-info" aria-label="Card back with contact details">
    <div class="wordmark">
      <div class="wordmark-name"><span>HALE &amp; HALE</span><span class="wordmark-dot"></span></div>
      <div class="wordmark-tagline">CERTIFIED PUBLIC ACCOUNTANTS</div>
    </div>
    <div class="divider"></div>
    <div class="person">
      <div class="person-name">Daniel Carter</div>
      <div class="person-title">Manager</div>
    </div>
    <ul class="contacts">
      <li><svg viewBox="0 0 16 16"><path fill="#9ccc2c" d="M4 1l3 3-2 2c1 2 3 4 5 5l2-2 3 3-2 3C7 15 1 9 1 3z"/></svg>555-014-7385</li>
      <li><svg viewBox="0 0 16 16"><rect x="1" y="3" width="14" height="10" fill="none" stroke="#9ccc2c" stroke-width="1.6"/><path d="M1 3l7 6 7-6" fill="none" stroke="#9ccc2c" stroke-width="1.6"/></svg>dcarter@halecpa.net</li>
      <li><svg viewBox="0 0 16 16"><circle cx="8" cy="8" r="7" fill="none" stroke="#9ccc2c" stroke-width="1.6"/><path d="M1 8h14M8 1c-3 4-3 10 0 14M8 1c3 4 3 10 0 14" fill="none" stroke="#9ccc2c" stroke-width="1.2"/></svg>www.halecpa.net</li>
    </ul>
    <address class="address">210 Ledger Street<br>Brookfield, OH 44403</address>
  </section>

  <section class="card card-brand" aria-label="Card front with firm name">
    <div class="mark-area" role="img" aria-label="Large faint embossed brand mark decoration"></div>
    <div class="wordmark">
      <div class="wordmark-name"><span>HALE &amp; HALE</span><span class="wordmark-dot"></span></div>
      <div class="wordmark-tagline">CERTIFIED PUBLIC ACCOUNTANTS</div>
    </div>
  </section>
</main>
</body>
</html>
```